Wholesale in Gold Jewellery & Gold Bullion

We are an established gold jewellery and gold bullion wholesaler selling these products to international clients. We already have a name and logo of our company, hence please view attached current card design. We need a completely new design to compliment our business and industry and the final design should be new and elegant.

Contact Information for Business Card

New card details must be same as per current card. Like logo, name, tel no. & etc.

Colors

Designer to choose colors to be used in the design.

```html
<!DOCTYPE html>
<html lang="en">
<head>
<meta charset="utf-8">
<title>Aurelin &amp; Co Business Card</title>
<link rel="stylesheet" href="https://fonts.googleapis.com/css2?family=Libre+Baskerville:wght@700&family=Montserrat:wght@400;500;600&display=swap">
<style>
  :root {
    --backdrop: #2b2a2a;
    --card: #f5f5f3;
    --ink-dark: #2a1d16;
    --ink-grey: #6f6f6f;
    --gold: #d79d28;
  }
  * { margin: 0; padding: 0; box-sizing: border-box; }
  html, body {
    width: 1200px; height: 901px; overflow: hidden;
    background: var(--backdrop);
  }
  .stage {
    width: 1200px; height: 901px;
    display: flex; align-items: center; justify-content: center;
  }
  .card {
    position: relative;
    width: 900px; height: 514px;
    background: var(--card);
    box-shadow: 0 18px 40px rgba(0,0,0,0.45);
    font-family: "Montserrat", sans-serif;
  }
  .brand {
    position: absolute; left: 120px; top: 150px;
    display: flex; align-items: center; gap: 36px;
  }
  .brand-dot {
    width: 84px; height: 84px; border-radius: 50%;
    background: var(--gold);
  }
  .brand-name {
    font-family: "Libre Baskerville", serif;
    font-weight: 700; font-size: 34px;
    color: var(--ink-dark); letter-spacing: 0.5px;
  }
  .person {
    position: absolute; right: 480px; top: 290px;
    text-align: right; color: var(--ink-grey);
  }
  .person-name { font-size: 40px; font-weight: 600; line-height: 1.1; }
  .person-role { font-size: 26px; font-weight: 400; margin-top: 2px; }
  .person-address { font-size: 22px; line-height: 1.35; margin-top: 34px; }
  .divider {
    position: absolute; left: 462px; top: 262px;
    width: 3px; height: 170px; background: var(--gold);
  }
  .contacts {
    position: absolute; left: 500px; top: 248px;
    list-style: none; color: var(--ink-grey);
    font-size: 22px; font-weight: 500;
  }
  .contacts li {
    display: flex; align-items: center; gap: 16px;
    height: 44px;
  }
  .contacts li:nth-child(2) { padding-left: 24px; }
  .contacts li:nth-child(3) { padding-left: 48px; }
  .contacts li:nth-child(4) { padding-left: 72px; }
  .contacts svg { width: 24px; height: 24px; flex: none; }
</style>
</head>
<body>
<div class="stage">
  <div class="card">
    <div class="brand">
      <div class="brand-dot"></div>
      <div class="brand-name">AURELIN &amp; CO PTE LTD</div>
    </div>

    <div class="person">
      <div class="person-name">Ravin Dasmore</div>
      <div class="person-role">Director</div>
      <div class="person-address">12 Lantern Hill Rd,<br>Singapore 208115</div>
    </div>

    <div class="divider"></div>

    <ul class="contacts">
      <li>
        <svg viewBox="0 0 24 24" aria-hidden="true"><rect x="6" y="2" width="12" height="20" rx="2" fill="none" stroke="#d79d28" stroke-width="2"/><circle cx="12" cy="18" r="1.2" fill="#d79d28"/></svg>
        <span>+65 9123 4501</span>
      </li>
      <li>
        <svg viewBox="0 0 24 24" aria-hidden="true"><path d="M6 3l4 1 1 4-2 2c1 2 3 4 5 5l2-2 4 1 1 4-2 2C11 20 4 13 4 5z" fill="#d79d28"/></svg>
        <span>+65 6100 2200</span>
      </li>
      <li>
        <svg viewBox="0 0 24 24" aria-hidden="true"><rect x="7" y="2" width="10" height="8" fill="none" stroke="#d79d28" stroke-width="2"/><rect x="3" y="10" width="18" height="11" rx="2" fill="#d79d28"/><rect x="7" y="14" width="10" height="2" fill="#f5f5f3"/></svg>
        <span>+65 6200 4815</span>
      </li>
      <li>
        <svg viewBox="0 0 24 24" aria-hidden="true"><rect x="2" y="5" width="20" height="14" fill="#d79d28"/><path d="M2 5l10 8 10-8" fill="none" stroke="#f5f5f3" stroke-width="1.6"/></svg>
        <span>ravin@aurelinco.com</span>
      </li>
    </ul>
  </div>
</div>
</body>
</html>
```